Fresh, modern, fun business card for pediatric dental practice

Need a business card for fresh, modern, fun pediatric dental practice

Clean look that matches our website's font and colors

We prefer the look of curved corners on business cards

Target Market(s)

parents (mothers) of young children, professionals, mid-high class

Industry/Entity Type

Dental

Contact Information for Business Card

Maplebrook Pediatric Dentistry
482 Quarry Lane
Suite 517
Cedarvale, ST 00517
555.555.0193
www.maplebrookkidsdental.example

Mei-Ran Tsai, DMD
Corinne Walbeck, DMD
(we are working on our email address, but we would like that on the card as well)

Font styles to use
Sans Serif

Requirements
Must have
• All info; we would also like to make cards for individual staff members
• colors from our website and color palatte, attatched
• use same font and design as website for branding
Nice to have
• clean, simple card that has a pop of color
• we would like to see a few designs with our tag line "where smiles get brighter"
• we are not sure if we want to have it on there or not
• we would like to see a few designs incorporating the ribbon graphic on our website where the word WELCOME is

```html
<!DOCTYPE html>
<html lang="en">
<head>
<meta charset="utf-8">
<title>Maplebrook Pediatric Dentistry – Business Card</title>
<link href="https://fonts.googleapis.com/css2?family=Oswald:wght@500&family=Lato:wght@400;700&display=swap" rel="stylesheet">
<style>
  :root{
    --backdrop:#1e1e1e;
    --card:#262626;
    --card-edge:#2e2e2e;
    --sun-yellow:#f7b81f;
    --berry:#c8338f;
    --ink-light:#f2f2f2;
  }
  *{margin:0;padding:0;box-sizing:border-box}
  html,body{width:1200px;height:900px;overflow:hidden;background:var(--backdrop)}
  .sheet{position:relative;width:1200px;height:900px}
  .card{
    position:absolute;left:250px;width:700px;height:400px;
    background:linear-gradient(135deg,var(--card-edge),var(--card));
    border-radius:22px;overflow:hidden;
    box-shadow:0 14px 30px rgba(0,0,0,.45);
  }
  .card::after{
    content:"";position:absolute;left:0;right:0;bottom:0;height:8px;
    background:var(--sun-yellow);
  }
  .card--front{top:35px}
  .card--back{top:465px}

  /* front */
  .brand{
    position:absolute;left:0;right:0;top:135px;
    display:flex;align-items:center;justify-content:center;gap:14px;
  }
  .brand__dot{width:26px;height:26px;border-radius:50%;background:var(--sun-yellow)}
  .brand__name{
    font-family:'Lato',sans-serif;font-weight:700;font-size:36px;
    color:var(--sun-yellow);letter-spacing:.5px;
  }
  .front-web{
    position:absolute;left:0;right:0;top:290px;text-align:center;
    font-family:'Lato',sans-serif;font-size:18px;letter-spacing:2px;color:var(--ink-light);
  }
  .front-web .domain{color:var(--sun-yellow)}

  /* back */
  .person{position:absolute;right:390px;top:105px;text-align:right}
  .person__name{
    font-family:'Oswald',sans-serif;font-weight:500;font-size:40px;
    color:var(--sun-yellow);letter-spacing:.5px;text-transform:uppercase;line-height:1.1;
  }
  .person__title{font-family:'Lato',sans-serif;font-size:19px;color:var(--ink-light);margin-top:4px}
  .divider{position:absolute;left:333px;top:112px;width:2px;height:68px;background:var(--berry)}
  .contact{position:absolute;left:356px;top:108px;list-style:none;
    font-family:'Lato',sans-serif;font-size:15.5px;color:var(--ink-light)}
  .contact li{display:flex;align-items:center;gap:10px;height:25px}
  .contact svg{width:14px;height:14px;flex:none}
  .practice{position:absolute;left:0;right:0;top:285px;text-align:center;font-family:'Lato',sans-serif}
  .practice__name{font-weight:700;font-size:18px;color:var(--sun-yellow);letter-spacing:1px;text-transform:uppercase}
  .practice__address{font-size:18px;color:var(--ink-light);margin-top:3px}
</style>
</head>
<body>
<main class="sheet">
  <section class="card card--front">
    <div class="brand">
      <span class="brand__dot"></span>
      <span class="brand__name">Maplebrook Pediatric Dentistry</span>
    </div>
    <p class="front-web">www.<span class="domain">maplebrookkidsdental</span>.example</p>
  </section>

  <section class="card card--back">
    <div class="person">
      <h1 class="person__name">Corinne Walbeck</h1>
      <p class="person__title">DMD</p>
    </div>
    <span class="divider"></span>
    <ul class="contact">
      <li>
        <svg viewBox="0 0 24 24" fill="var(--sun-yellow)"><path d="M6.6 10.8a15.1 15.1 0 0 0 6.6 6.6l2.2-2.2a1 1 0 0 1 1-.25 11.4 11.4 0 0 0 3.6.57 1 1 0 0 1 1 1V20a1 1 0 0 1-1 1A17 17 0 0 1 3 4a1 1 0 0 1 1-1h3.5a1 1 0 0 1 1 1c0 1.250.2 2.45.57 3.57a1 1 0 0 1-.25 1z"/></svg>
        555.555.0193
      </li>
      <li>
        <svg viewBox="0 0 24 24" fill="var(--sun-yellow)"><path d="M2 5h20v14H2z"/><path d="M2 5l10 8 10-8" fill="none" stroke="#262626" stroke-width="2"/></svg>
        info@maplebrookkidsdental.example
      </li>
      <li>
        <svg viewBox="0 0 24 24" fill="none" stroke="var(--sun-yellow)" stroke-width="2"><circle cx="12" cy="12" r="10"/><path d="M2 12h20M12 2c3 3 3 17 0 20M12 2c-3 3-3 17 0 20"/></svg>
        www.maplebrookkidsdental.example
      </li>
    </ul>
    <div class="practice">
      <p class="practice__name">Maplebrook Pediatric Dentistry</p>
      <p class="practice__address">482 Quarry Lane Suite 517 Cedarvale, ST 00517</p>
    </div>
  </section>
</main>
</body>
</html>
```